Business Card Design

Company is a Commercial Building Company specialising in New Construction and existing refurbishments

Industry/Entity Type

Business

Contact Information for Business Card

Liam Porter
Construction Manager
E Liam@marshbuilding.com.au
M 0400 213 594
Mail 14 Tarrant Rise Seabrook WA 6215

```html
<!DOCTYPE html>
<html lang="en">
<head>
<meta charset="utf-8">
<title>Marsh Building &amp; Construction – Business Card</title>
<link rel="stylesheet" href="https://fonts.googleapis.com/css2?family=Exo+2:wght@400;500;600;700&display=swap">
<style>
  :root {
    --navy: #343a4e;
    --cyan: #06bcd8;
    --orange: #f58a1f;
    --white: #ffffff;
    --backdrop: #e4e6e3;
  }
  * { margin: 0; padding: 0; box-sizing: border-box; }
  html, body { width: 1200px; height: 777px; overflow: hidden; }
  body {
    background: var(--backdrop);
    font-family: "Exo 2", Arial, sans-serif;
    position: relative;
  }
  .card {
    position: absolute;
    top: 137px;
    width: 322px;
    height: 561px;
    overflow: hidden;
    box-shadow: 0 4px 14px rgba(0,0,0,0.18);
  }
  .card--front { left: 180px; background: var(--white); }
  .card--back { left: 698px; background: var(--navy); }

  .brand-square {
    position: absolute;
    left: 50%;
    top: 50px;
    width: 80px;
    height: 80px;
    margin-left: -40px;
    background: var(--cyan);
  }
  .card--back .brand-square { top: 55px; }
  .brand-name {
    position: absolute;
    top: 157px;
    left: 0; right: 0;
    text-align: center;
  }
  .brand-name__main {
    display: block;
    font-weight: 700;
    font-size: 23px;
    line-height: 25px;
    letter-spacing: 0.3px;
  }
  .brand-name__sub {
    display: block;
    font-weight: 400;
    font-size: 20px;
    line-height: 22px;
    letter-spacing: 0.2px;
  }
  .card--front .brand-name { color: var(--navy); }
  .card--back .brand-name { color: var(--white); top: 162px; }

  .skyline {
    position: absolute;
    left: 0; right: 0;
    top: 233px;
    height: 94px;
  }
  .card--front .skyline { background: linear-gradient(to bottom, var(--white) 0%, var(--navy) 70%); }
  .card--back .skyline { background: linear-gradient(to bottom, var(--navy) 0%, var(--white) 70%); }

  .contact-panel {
    position: absolute;
    left: 0; right: 0;
    top: 327px;
    height: 198px;
    background: var(--navy);
    color: var(--white);
    text-align: center;
  }
  .person-name {
    margin-top: 34px;
    font-weight: 700;
    font-size: 27px;
    line-height: 30px;
    letter-spacing: 0.3px;
    color: var(--orange);
  }
  .person-role { font-size: 16px; line-height: 20px; letter-spacing: 0.3px; }
  .contact-lines {
    margin-top: 40px;
    font-size: 19px;
    line-height: 23px;
    letter-spacing: 0.3px;
  }

  .address-panel {
    position: absolute;
    left: 0; right: 0;
    top: 327px;
    height: 202px;
    background: var(--white);
    color: var(--navy);
    text-align: center;
  }
  .address {
    margin-top: 85px;
    font-size: 22px;
    line-height: 27px;
    letter-spacing: 0.5px;
  }

  .band {
    position: absolute;
    left: 0; right: 0;
    bottom: 0;
    height: 36px;
  }
  .band--cyan { background: var(--cyan); }
  .band--orange { background: var(--orange); height: 32px; }
</style>
</head>
<body>
  <section class="card card--front">
    <div class="brand-square"></div>
    <div class="brand-name">
      <span class="brand-name__main">MARSH BUILDING</span>
      <span class="brand-name__sub">&amp; CONSTRUCTION</span>
    </div>
    <div class="skyline" role="img" aria-label="City skyline silhouette with bridge"></div>
    <div class="contact-panel">
      <p class="person-name">LIAM PORTER</p>
      <p class="person-role">Construction Manager</p>
      <p class="contact-lines">0400 213 594<br>Liam@marshbuilding.com.au</p>
    </div>
    <div class="band band--cyan"></div>
  </section>

  <section class="card card--back">
    <div class="brand-square"></div>
    <div class="brand-name">
      <span class="brand-name__main">MARSH BUILDING</span>
      <span class="brand-name__sub">&amp; CONSTRUCTION</span>
    </div>
    <div class="skyline" role="img" aria-label="City skyline silhouette with bridge"></div>
    <div class="address-panel">
      <p class="address">14 Tarrant Rise<br>Seabrook WA 6215</p>
    </div>
    <div class="band band--orange"></div>
  </section>
</body>
</html>
```